Modern web-site for a game changer new health app!

We need a very clean UX / UI design for our company website that will be used to sell our brand to large corporations and their employees. If we find a good match, we'd need you to do the app design and some graphics for ongoing design needs.

For a first of its kind app developed at Brockwell University, making licensed holistic medicine accessible to everyday people through access and curation by democratizing holistic health.

Please read the details attached thoroughly and reach out if you have any questions. Many thanks!
Updates

I've updated our requirements to make it easier, please review new details in the PDF shared. Many thanks!

Final brief refinement just uploaded, much has been simplified with very clear guidelines, please update and apply. thanks much!

Target Market(s)

corporate employees and large C level corporate leaders

Industry/Entity Type

wellness

Number of Pages Required

4 page

Font styles to use
Other font styles liked:
• We need website design now and app and socials after, hoping the designer we choose now can work with us on a regular basis going forward

Requirements
Must have
• clean, modern, minimal rich
Nice to have
• some added touches to give a custom feel
Should not have
• pictures, natural looking images or shapes

```html
<!DOCTYPE html>
<html lang="en">
<head>
<meta charset="utf-8">
<title>Avela — Wellness for Everyone</title>
<link href="https://fonts.googleapis.com/css2?family=Outfit:wght@300;400;500;600;700&display=swap" rel="stylesheet">
<style>
:root{
  --orange:#e8850c;
  --orange-dark:#d06f00;
  --forest:#1f2e17;
  --forest-soft:#2b3d22;
  --ink:#1b1b1b;
  --olive:#a8b43a;
  --sage:#8fa67c;
  --mist:#eef1ec;
  --white:#ffffff;
  --text:#2a2a2a;
  --muted:#6b6b6b;
}
*{box-sizing:border-box;margin:0;padding:0}
html,body{width:1200px;height:5305px;overflow:hidden}
body{font-family:"Outfit",sans-serif;color:var(--text);background:var(--white);position:relative}
.abs{position:absolute}
.btn{display:inline-flex;align-items:center;justify-content:center;background:var(--orange);color:#fff;border-radius:30px;font-size:15px;letter-spacing:1px;text-transform:uppercase;font-weight:500}
.brand{font-family:"Outfit",sans-serif;font-weight:600;color:var(--orange);letter-spacing:4px}

/* header */
.site-header{position:absolute;top:0;left:0;width:1200px;height:110px;background:#fff}
.site-header .brand{left:112px;top:26px;font-size:46px}
.nav{position:absolute;left:476px;top:40px;display:flex;gap:36px;font-size:15px;letter-spacing:1px;color:#333}
.nav .active{color:var(--orange);border-bottom:2px solid var(--orange);padding-bottom:4px}
.site-header .btn{left:928px;top:30px;width:162px;height:46px}

/* hero */
.hero{top:110px;left:0;width:1200px;height:520px;background:radial-gradient(ellipse at 50% 40%,#3a5a2a,#25381a 55%,#4d7a2f 100%)}
.hero h1{position:absolute;top:72px;width:100%;text-align:center;color:#fff;font-size:50px;font-weight:400;letter-spacing:2px}
.hero h1 b{font-weight:700}
.hero .sub{position:absolute;top:152px;width:100%;text-align:center;color:#fff;font-size:31px;font-weight:300;letter-spacing:1px}
.hero .small{position:absolute;top:204px;width:100%;text-align:center;color:#fff;font-size:19px}
.hero .btn{position:absolute;left:519px;top:274px;width:164px;height:44px}

/* process panel */
.process{left:82px;top:516px;width:1036px;height:420px;background:var(--ink);border-radius:18px}
.step{position:absolute;top:70px;width:364px;height:280px;text-align:center}
.step .ico{width:90px;height:90px;border-radius:50%;margin:24px auto 0;display:flex;align-items:center;justify-content:center}
.step h3{margin-top:28px;font-size:20px;font-weight:400;color:var(--orange)}
.step p{margin:16px auto 0;width:240px;font-size:13px;line-height:25px;color:#ddd}
.step.featured{background:#fff;border-radius:12px}
.step.featured h3{color:#222}
.step.featured p{color:#777}

/* offerings */
.offer-bg{top:936px;left:0;width:1200px;height:820px;background:linear-gradient(180deg,#f4f6f2 0%,#dfe7d9 50%,#b2c4a6 100%)}
.tile{position:absolute;width:297px;background:var(--forest);border-radius:10px;overflow:hidden}
.tile .ph{height:212px;background:linear-gradient(135deg,#c9ccd4,#e9e9ee)}
.tile span{display:block;padding:16px 24px;color:#fff;font-size:17px;letter-spacing:1px;line-height:26px}

/* how it works */
.how{top:1740px;left:0;width:1200px;height:626px;background:var(--forest)}
.how h2{position:absolute;top:156px;width:100%;text-align:center;color:#fff;font-size:42px;font-weight:500;letter-spacing:2px}
.how p{position:absolute;width:100%;text-align:center;color:#e5e5e5;font-size:15px;line-height:24px}
.flow{position:absolute;top:350px;left:340px;width:540px;height:110px}
.flow .lbl{position:absolute;color:#eee;font-size:15px;text-align:center;line-height:19px}
.how .btn{position:absolute;left:517px;top:486px;width:164px;height:44px}

/* enterprise */
.enterprise{top:2366px;left:0;width:1200px;height:508px;background:var(--ink)}
.enterprise h2{position:absolute;left:113px;top:104px;color:#fff;font-size:30px;font-weight:500;letter-spacing:1px}
.enterprise .lead{position:absolute;left:118px;top:162px;color:#fff;font-size:21px}
.check{position:absolute;left:130px;width:470px;color:#ddd;font-size:15px;line-height:23px;padding-left:32px}
.check svg{position:absolute;left:0;top:6px}
.enterprise .btn{position:absolute;left:113px;top:372px;width:276px;height:44px}
.enterprise .ph{position:absolute;left:632px;top:100px;width:457px;height:329px;border-radius:10px;background:linear-gradient(135deg,#c5b8a4,#8b8f86 55%,#596a7a)}

/* trusted */
.trusted{top:2874px;left:0;width:1200px;height:650px;background:linear-gradient(180deg,#fbfcfa,#eef1e8)}
.pill{position:absolute;left:0;top:98px;width:681px;height:96px;background:var(--forest);border-radius:0 48px 48px 0;color:#fff;display:flex;align-items:center;padding-left:115px;font-size:31px;font-weight:600;gap:18px}
.pill small{font-size:29px;font-weight:600}
.pill b{font-size:40px;font-weight:600}
.trusted h2{position:absolute;top:248px;width:100%;text-align:center;font-size:33px;font-weight:400;letter-spacing:1px;line-height:44px;color:#222}
.feat{position:absolute;top:412px;width:248px;height:138px;background:var(--forest);border:3px solid var(--orange);border-radius:12px;color:#fff;text-align:center;font-size:20px}
.feat .ico{position:absolute;left:72px;top:-70px;width:104px;height:104px;border-radius:50%;background:var(--orange);display:flex;align-items:center;justify-content:center}
.feat span{position:absolute;left:0;right:0;top:80px}

/* human care */
.care{top:3524px;left:0;width:1200px;height:990px;background:var(--forest)}
.care h2{position:absolute;top:84px;width:100%;text-align:center;color:#fff;font-size:33px;font-weight:400;letter-spacing:1px}
.care .intro{position:absolute;top:150px;width:100%;text-align:center;color:#fff;font-size:20px;line-height:29px}
.stat{position:absolute;top:248px;width:392px;height:262px;background:#fff;border:6px solid var(--olive);border-radius:14px;text-align:center;color:#333}
.stat p{font-size:20px;line-height:31px}
.quote{position:absolute;background:var(--sage);border-radius:10px;color:#fff;font-size:12.5px;line-height:24px;text-align:center;overflow:hidden}
.quote.center{background:var(--ink);z-index:2}
.quote b{display:block;font-size:15px;margin-top:8px}
.dot{position:absolute;top:886px;width:14px;height:14px;border-radius:50%;background:var(--olive)}

/* contact */
.contact{top:4504px;left:0;width:1200px;height:456px;background:var(--forest)}
.contact h3{position:absolute;color:#fff;font-weight:400;letter-spacing:1px}
.field{position:absolute;height:50px;border:1px solid #ccc;background:#fff;border-radius:4px;padding:14px 20px;font-size:14px;color:#333}
.contact .btn{position:absolute;left:740px;top:464px;width:214px;height:46px;z-index:3}
.footer{top:4940px;left:0;width:1200px;height:365px;background:var(--ink)}
</style>
</head>
<body>

<header class="site-header">
  <div class="brand abs">AVELA</div>
  <nav class="nav"><span class="active">COMPLEMENTARY</span><span>ENTERPRISE</span><span>MEMBERS</span></nav>
  <a class="btn abs">Get Started</a>
</header>

<section class="hero abs" role="img" aria-label="Close-up of white flowers among green leaves">
  <h1><b>WELLNESS</b> FOR EVERYONE</h1>
  <div class="sub">Morden Science Meets Ancient Wistom</div>
  <div class="small">Get 1 on 1 PHD care on US for personalized remedies</div>
  <a class="btn">Get Started</a>
</section>

<section class="offer-bg abs">
  <div class="tile" style="left:113px;top:120px"><div class="ph" role="img" aria-label="Person in a yoga stretch"></div><span>1 ON 1 WITH HOLISTIC<br>DOCTORS &amp; UNLIMITED</span></div>
  <div class="tile" style="left:455px;top:120px"><div class="ph" role="img" aria-label="Glass bottles with a plant sprout"></div><span>PERSONALIZED CUSTOM<br>SUPPLEMENTS</span></div>
  <div class="tile" style="left:796px;top:120px"><div class="ph" role="img" aria-label="Person resting by a window"></div><span>GUT, HORMONE &amp;<br>CELLULAR LAB TESTS</span></div>
  <div class="tile" style="left:113px;top:480px"><div class="ph" role="img" aria-label="Person in relaxed clothing"></div><span style="padding:26px 24px">UNLIMITED CLASSES</span></div>
  <div class="tile" style="left:455px;top:480px"><div class="ph" role="img" aria-label="Person meditating by the sea"></div><span>FREE YOGA, MEDITATION<br>&amp; HEALTH ESSENTIALS BY</span></div>
  <div class="tile" style="left:796px;top:480px"><div class="ph" role="img" aria-label="Hands in a calming massage"></div><span style="padding:26px 24px">WORKSHOPS</span></div>
</section>

<section class="process abs">
  <div class="step" style="left:38px">
    <div class="ico" style="background:#fff"><svg width="44" height="50" viewBox="0 0 44 50" fill="none" stroke="#222" stroke-width="2"><rect x="6" y="4" width="30" height="40" rx="3"/><path d="M12 14h18M12 21h18M12 28h10"/><path d="M26 34l4 4 8-10"/></svg></div>
    <h3>Take Test</h3>
    <p>Sed ornare, turpis eu aliquet placerat, nisi erat pharetra nunc, ac lacinia massa urna ut diam.</p>
  </div>
  <div class="step featured" style="left:336px">
    <div class="ico" style="background:var(--orange)"><svg width="46" height="50" viewBox="0 0 46 50" fill="none" stroke="#222" stroke-width="2"><circle cx="23" cy="16" r="9"/><path d="M6 46c0-10 8-16 17-16s17 6 17 16"/><path d="M17 32v8M29 32v6"/></svg></div>
    <h3>Get Matched with a Specialist</h3>
    <p>Sed ornare, turpis eu aliquet placerat, nisi erat pharetra nunc, ac lacinia massa urna ut diam.</p>
  </div>
  <div class="step" style="left:634px">
    <div class="ico" style="background:#fff"><svg width="50" height="44" viewBox="0 0 50 44" fill="none" stroke="#222" stroke-width="2"><rect x="4" y="8" width="38" height="26" rx="2"/><path d="M2 38h44"/><circle cx="23" cy="19" r="5"/><rect x="32" y="2" width="14" height="10" rx="2"/></svg></div>
    <h3>Video Consult</h3>
    <p>To get full read on your unique needs + natural remedies-diet-lifestyle - exercise - home &amp; body</p>
  </div>
</section>

<section class="how abs">
  <svg class="abs" style="left:0;top:-20px" width="1200" height="60" viewBox="0 0 1200 60"><path d="M0 30 Q600 -20 1200 30 V60 H0z" fill="#1f2e17"/></svg>
  <h2>HOW IT WORKS:</h2>
  <p style="top:222px">Sign-up and get a full read of your unique constitution and what makes it thrive with a custom<br>plan made one on one with your on-demand holistic Doctor/Educator.</p>
  <p style="top:290px">Unlimited texting to address your plan or any other concern you have about your health.</p>
  <div class="flow">
    <svg class="abs" style="left:20px;top:0" width="44" height="30" fill="none" stroke="#fff" stroke-width="2"><path d="M4 16l8 8 14-20M16 24l22-20"/></svg>
    <div class="lbl" style="left:0;top:44px;width:84px">Sign Up</div>
    <svg class="abs" style="left:94px;top:50px" width="60" height="10"><path d="M0 5h54M48 1l6 4-6 4" stroke="#fff" fill="none"/></svg>
    <svg class="abs" style="left:206px;top:0" width="40" height="40" fill="none" stroke="#fff" stroke-width="2"><circle cx="20" cy="20" r="15" stroke-dasharray="3 3"/><circle cx="20" cy="20" r="7"/></svg>
    <div class="lbl" style="left:156px;top:44px;width:140px">Get a full read<br>of your constitution</div>
    <svg class="abs" style="left:310px;top:50px" width="60" height="10"><path d="M0 5h54M48 1l6 4-6 4" stroke="#fff" fill="none"/></svg>
    <svg class="abs" style="left:420px;top:0" width="44" height="36" fill="none" stroke="#fff" stroke-width="2"><path d="M4 28c6 0 10-4 16-4h12M22 16c-4-6 0-12 6-12 0 6-2 10-6 12zM22 16c4-4 10-4 14-2-2 4-8 6-14 2"/></svg>
    <div class="lbl" style="left:370px;top:44px;width:160px">Get a custom plan</div>
  </div>
  <a class="btn">View Plans</a>
</section>

<section class="enterprise abs">
  <svg class="abs" style="left:0;top:-18px" width="1200" height="40" viewBox="0 0 1200 40"><path d="M0 36 Q600 0 1200 10 V40 H0z" fill="#1b1b1b"/></svg>
  <h2>AVELA FOR ENTERPRISE</h2>
  <div class="lead">We're all feeling a strain on our health these days</div>
  <div class="check" style="top:218px"><svg width="22" height="16" fill="none" stroke="#fff" stroke-width="2.5"><path d="M2 8l6 6L20 2"/></svg>Leaders of industry aren't accidental, they know employee retention &amp; experience work in their favor.</div>
  <div class="check" style="top:292px"><svg width="22" height="16" fill="none" stroke="#fff" stroke-width="2.5"><path d="M2 8l6 6L20 2"/></svg>In these tumultuous times, Solace brings much-needed relief and benefits to teams that bring their all in return.</div>
  <a class="btn">Avela for Enterprise</a>
  <div class="ph" role="img" aria-label="Group yoga class stretching on mats in a bright studio"></div>
</section>

<section class="trusted abs">
  <div class="pill"><small>Trusted by:</small><b>Northfield Outfitters</b></div>
  <h2>OUR CLIENTS TRUST US TO PROVIDE HOLISTIC<br>HEALTH FOR THEIR TEAM, SO SHOULD YOU!</h2>
  <div class="feat" style="left:170px"><div class="ico"><svg width="54" height="54" fill="none" stroke="#222" stroke-width="2"><circle cx="27" cy="27" r="20"/><circle cx="27" cy="27" r="9"/><path d="M27 3v8M27 43v8M3 27h8M43 27h8"/></svg></div><span>Any Challenge</span></div>
  <div class="feat" style="left:470px"><div class="ico"><svg width="54" height="54" fill="none" stroke="#222" stroke-width="2"><circle cx="27" cy="29" r="19"/><path d="M27 18v11l7 6M20 6h14"/></svg></div><span>Any Time</span></div>
  <div class="feat" style="left:769px"><div class="ico"><svg width="56" height="54" fill="none" stroke="#222" stroke-width="2"><rect x="4" y="18" width="30" height="22" rx="3"/><path d="M10 26h18M10 32h12"/><circle cx="42" cy="16" r="8"/><path d="M32 44c0-6 4-10 10-10s10 4 10 10"/></svg></div><span>Any Where</span></div>
</section>

<section class="care abs">
  <h2>HUMAN CARE POWERED BY TECHNOLOGY</h2>
  <div class="intro">All Your Mind Body Needs Met In One Place. All practitioners<br>work collaboratively to provide the best care.</div>
  <div class="stat" style="left:160px">
    <p style="margin-top:34px">Clinically proven to help<br>people not only feel better,<br>but thrive.</p>
    <div class="abs" style="left:62px;top:148px;font-size:42px;font-weight:600">80%<div style="font-size:20px;font-weight:500;margin-top:-6px">Avela</div></div>
    <div class="abs" style="left:202px;top:148px;font-size:42px;font-weight:600">20%<div style="font-size:14px;font-weight:500;line-height:18px;margin-top:0">Leading corporate<br>health programs</div></div>
  </div>
  <div class="stat" style="left:646px">
    <p style="margin-top:34px">Members love the easy &amp;<br>effective experience</p>
    <div style="font-size:42px;font-weight:600;margin-top:4px">5<svg width="32" height="30" viewBox="0 0 24 24"><path d="M12 2l3 7 7 .6-5.3 4.7 1.6 7.2L12 17.8 5.7 21.5l1.6-7.2L2 9.6 9 9z" fill="#a8b43a"/></svg></div>
    <p style="margin-top:6px">average rating after every<br>care session.</p>
  </div>
  <div class="quote" style="left:28px;top:622px;width:360px;height:194px;padding:32px 20px 0 34px">Anytime I'm feeling tired or stressed I just get up and pass by the classes by Solace and I'm instantly relaxed, it's easy and I frequently ask for more to be added and are getting along better.<b>—DAISY | HUMAN</b></div>
  <div class="quote" style="left:814px;top:622px;width:360px;height:194px;padding:28px 34px 0 18px">I had no idea that being healthy would actually be this easy and fun. Workouts and nutrition used to be a source of stress for me. It's so interesting how proper knowledge and<b>— CARRIE | FIELD</b></div>
  <div class="quote center" style="left:378px;top:604px;width:448px;height:240px;padding:30px 28px 0">
    <svg class="abs" style="left:44px;top:26px" width="40" height="32" viewBox="0 0 40 32"><path d="M2 30V18C2 8 8 3 16 2v6c-4 1-6 4-6 8h6v14zM22 30V18c0-10 6-15 14-16v6c-4 1-6 4-6 8h6v14z" fill="#e8850c"/></svg>
    <div style="font-size:14px;line-height:29px;padding-left:64px;text-align:left">I'm so glad that I chose Solace for our</div>
    <div style="font-size:14px;line-height:29px">company. Who knew that something that I could just expense from petty cash would transform the lives of so many people here including myself.</div>
    <b style="font-size:17px;margin-top:14px">— IRIS | ACCOUNTING</b>
  </div>
  <div class="dot" style="left:568px"></div><div class="dot" style="left:593px;background:#111"></div><div class="dot" style="left:620px"></div>
</section>

<section class="contact abs">
  <h3 style="left:113px;top:102px;font-size:30px;line-height:42px">WE'D LOVE TO HEAR<br>FROM YOU</h3>
  <p class="abs" style="left:115px;top:210px;width:470px;color:#eee;font-size:15px;line-height:33px">Tell us a little about you and your company to see if you qualify for our membership-based model at no cost to your company.</p>
  <div class="abs" style="left:115px;top:356px;color:#fff;font-size:15px;font-weight:600">EMAIL:</div>
  <svg class="abs" style="left:115px;top:392px" width="30" height="22"><rect x="1" y="1" width="28" height="20" rx="2" fill="#fff"/><path d="M2 3l13 10L28 3" stroke="#1f2e17" stroke-width="2" fill="none"/></svg>
  <div class="abs" style="left:162px;top:392px;color:#fff;font-size:16px">info@avelaforhealth.example</div>
  <h3 style="left:626px;top:82px;font-size:31px">CONTACT US</h3>
  <div class="field" style="left:626px;top:146px;width:200px">Name</div>
  <div class="field" style="left:860px;top:146px;width:206px">Phone number</div>
  <div class="field" style="left:626px;top:226px;width:440px">How many locations?</div>
  <div class="field" style="left:626px;top:306px;width:440px">How many people in your location?</div>
  <div class="field" style="left:626px;top:386px;width:440px">Anything else we can help you with?</div>
  <a class="btn">Submit</a>
</section>

<footer class="footer abs">
  <svg class="abs" style="left:0;top:-50px" width="1200" height="90" viewBox="0 0 1200 90"><path d="M0 20 Q400 110 1200 40 V90 H0z" fill="#1b1b1b"/></svg>
  <div class="brand abs" style="left:196px;top:196px;font-size:62px">AVELA</div>
  <div class="abs" style="left:598px;top:196px;width:300px;height:56px;background:#fff;padding:18px 30px;font-size:18px;color:#333">Enter you email here *</div>
  <div class="abs" style="left:898px;top:196px;width:108px;height:56px;background:var(--orange);display:flex;align-items:center;justify-content:center"><svg width="40" height="20"><path d="M2 10h32M26 3l8 7-8 7" stroke="#fff" stroke-width="4" fill="none"/></svg></div>
  <div class="abs" style="left:602px;top:272px;color:#fff;font-size:13px">© 2021 Solace | All rights reserved.</div>
</footer>

</body>
</html>
```